Homemaking training schools needs a Business Card design

Designer, Hello!

No special requirements, good-looking enough.
--------------------------------------------------------------------------

Name: Marcus Dole
Chairman
Tel: 0574-71948263
Mobile: 13857420916
Email: kelvora@mailnest.example
Web: www.prt2019.example
Add: No.258, LanpingJie, BeiyuanQu, Ningbo, Zhejiang

LOGO
Ningbo PRT Homemaking Training School

Target Market(s)

pregnant women, mothers, infants, the elderly and families, including cleaning, cooking, nursing training.

Industry/Entity Type

Business

Contact Information for Business Card

Name: Marcus Dole
Chairman
Tel: 0574-71948263
Mobile: 13857420916
Email: kelvora@mailnest.example
Web: www.prt2019.example

LOGO

Font styles to use
Serif
Sans Serif
Decorative

Requirements
Nice to have
• Feels: clean, specifications, safety, comfort, warmth and happiness.

```html
<!DOCTYPE html>
<html lang="en">
<head>
<meta charset="utf-8">
<title>PinRuiTang Business Card</title>
<link rel="stylesheet" href="https://fonts.googleapis.com/css2?family=Lato:wght@300;400;700&display=swap">
<style>
  :root {
    --brand-blue: #3a7bbf;
    --brand-magenta: #c2178f;
    --ink: #1c1c1c;
    --paper: #ffffff;
    --stage: #e9eaed;
  }
  * { box-sizing: border-box; margin: 0; padding: 0; }
  html, body { width: 1200px; height: 900px; overflow: hidden; }
  body {
    background: var(--stage);
    font-family: "Lato", Arial, sans-serif;
    position: relative;
  }
  .card {
    position: absolute;
    left: 250px;
    width: 700px;
    height: 400px;
    box-shadow: 0 8px 24px rgba(0,0,0,0.18);
    overflow: hidden;
  }
  .card--back { top: 35px; background: var(--brand-blue); color: var(--paper); }
  .card--front { top: 465px; background: var(--paper); color: var(--ink); }

  /* back side lockup */
  .lockup { position: absolute; left: 0; right: 0; top: 120px; text-align: center; }
  .lockup__name {
    font-weight: 700;
    font-size: 58px;
    letter-spacing: 0.5px;
    line-height: 1;
  }
  .lockup__rule {
    display: flex; align-items: center; justify-content: center; gap: 14px;
    margin-top: 14px;
    font-weight: 300; font-size: 22px; letter-spacing: 1px;
  }
  .lockup__rule::before, .lockup__rule::after {
    content: ""; width: 110px; height: 1.5px; background: currentColor;
  }
  .lockup__web {
    margin-top: 40px;
    font-size: 18px; letter-spacing: 4px;
  }

  /* front side */
  .front-art { position: absolute; inset: 0; }
  .front-logo { position: absolute; left: 44px; top: 38px; color: var(--brand-blue); }
  .front-logo .lockup__name { font-size: 44px; }
  .front-logo .lockup__rule { font-size: 16px; margin-top: 8px; justify-content: flex-start; color: #333; }
  .front-logo .lockup__rule::before, .front-logo .lockup__rule::after { width: 60px; height: 1px; }

  .address {
    position: absolute; left: 62px; top: 150px;
    font-size: 17px; line-height: 1.3;
  }
  .contacts {
    position: absolute; left: 44px; top: 205px;
    list-style: none; font-size: 17px; line-height: 1.45;
  }
  .contacts li { display: flex; align-items: center; gap: 8px; }
  .contacts svg { width: 12px; height: 12px; fill: var(--brand-magenta); flex: none; }

  .holder {
    position: absolute; right: 70px; bottom: 36px; text-align: left;
  }
  .holder__name { color: var(--paper); font-size: 34px; font-weight: 400; }
  .holder__role { color: var(--brand-magenta); font-size: 20px; margin-top: -2px; }
</style>
</head>
<body>

<section class="card card--back" aria-label="Card back">
  <div class="lockup">
    <div class="lockup__name">PinRuiTang</div>
    <div class="lockup__rule">Training &amp; Services</div>
    <div class="lockup__web">www.prt2019.example</div>
  </div>
</section>

<section class="card card--front" aria-label="Card front">
  <svg class="front-art" viewBox="0 0 700 400" preserveAspectRatio="none" aria-hidden="true">
    <path d="M0,300 C180,345 470,350 600,210 C650,150 680,70 700,20 L700,400 L0,400 Z" fill="var(--brand-blue)"/>
    <path d="M440,306 C575,290 645,175 676,6 L700,6 L700,14 C670,160 600,290 440,306 Z" fill="var(--paper)"/>
    <path d="M430,304 C565,285 640,170 668,6 L690,6 C660,165 585,290 430,304 Z" fill="var(--brand-magenta)"/>
  </svg>

  <div class="front-logo">
    <div class="lockup__name">PinRuiTang</div>
    <div class="lockup__rule">Training &amp; Services</div>
  </div>

  <p class="address">No.258, LanpingJie<br>BeiyuanQu, Ningbo, Zhejiang</p>

  <ul class="contacts">
    <li><svg viewBox="0 0 12 12"><path d="M2.5 1 L4.5 1 L5 3.5 L3.8 4.5 C4.4 6 5.8 7.5 7.5 8.2 L8.5 7 L11 7.5 L11 9.5 C11 10.5 10 11 9 11 C4.5 10.5 1.5 7.5 1 3 C1 2 1.5 1 2.5 1 Z"/></svg>0574-71948263</li>
    <li><svg viewBox="0 0 12 12"><path d="M3 0.5 H9 V11.5 H3 Z M4 1.5 V8.5 H8 V1.5 Z M5.5 9.5 H6.5 V10.5 H5.5 Z"/></svg>1385-7420916</li>
    <li><svg viewBox="0 0 12 12"><path d="M0.5 2.5 H11.5 V9.5 H0.5 Z M1.5 3.3 L6 6.5 L10.5 3.3 V3 H1.5 Z"/></svg>kelvora@mailnest.example</li>
    <li><svg viewBox="0 0 12 12"><circle cx="6" cy="6" r="5.5"/></svg>www.prt2019.example</li>
  </ul>

  <div class="holder">
    <div class="holder__name">Marcus Dole</div>
    <div class="holder__role">Chairman</div>
  </div>
</section>

</body>
</html>
```